Health Spectrum and Energy Slides

Create beautiful and facinating PowerPoint slides that inspire and motivate

Target Market(s)

Clients looking for strategic breakthroughs and transformation

Industry/Entity Type

Health

Requirements
Must have
• Beautiful, heartfelt and fascinating graphics.
Nice to have
• Award winning designs.

```html
<!DOCTYPE html>
<html lang="en">
<head>
<meta charset="utf-8">
<title>Health Spectrum Slides</title>
<link href="https://fonts.googleapis.com/css2?family=Open+Sans:wght@400;600;700;800&family=Montserrat:wght@800&display=swap" rel="stylesheet">
<style>
  :root{
    --board:#f5f5f5;
    --frame:#cfd2d4;
    --title-blue:#2b5aa6;
    --ink:#141414;
    --white:#ffffff;
    --label-grey:#8a8f92;
    --divider:#e0633a;
    --placeholder:#b3bcbf;
  }
  html,body{margin:0;padding:0;overflow:hidden;}
  body{width:1200px;height:746px;background:var(--board);position:relative;font-family:"Open Sans",sans-serif;}
  .slide{position:absolute;width:555px;height:325px;border:1px solid var(--frame);box-sizing:border-box;background:var(--white);}
  .slide svg{display:block;width:100%;height:100%;}
  .slide-one{left:19px;top:11px;}
  .slide-two{left:603px;top:11px;}
  .slide-three{left:19px;top:389px;}
  .slide-number{position:absolute;font-weight:700;font-size:16px;color:var(--label-grey);}
  .num-one{left:21px;top:341px;}
  .num-two{left:605px;top:341px;}
  .num-three{left:21px;top:719px;}
  .section-divider{position:absolute;left:589px;top:379px;width:1.5px;height:345px;background:var(--divider);}
  .section-placeholder{position:absolute;left:650px;top:470px;width:450px;text-align:center;font-family:"Montserrat",sans-serif;font-weight:800;font-size:112px;line-height:1;letter-spacing:2px;color:var(--placeholder);}
  .t-title{font-weight:700;font-size:11px;}
  .t-label{font-weight:700;font-size:10px;}
  .t-small{font-weight:400;font-size:7.2px;}
</style>
</head>
<body>

<!-- Slide 1 -->
<div class="slide slide-one">
<svg viewBox="0 0 694 406" preserveAspectRatio="none">
  <defs>
    <linearGradient id="s1-sky" x1="0" y1="0" x2="1" y2="0">
      <stop offset="0" stop-color="#f6c21a"/><stop offset="0.25" stop-color="#d9c98e"/>
      <stop offset="0.5" stop-color="#6f7472"/><stop offset="1" stop-color="#2a2c2e"/>
    </linearGradient>
    <radialGradient id="s1-sun" cx="0.1" cy="0.55" r="0.35">
      <stop offset="0" stop-color="#fff3a8"/><stop offset="1" stop-color="#fff3a8" stop-opacity="0"/>
    </radialGradient>
    <linearGradient id="s1-sea" x1="0" y1="0" x2="1" y2="0">
      <stop offset="0" stop-color="#1f6fb0"/><stop offset="0.3" stop-color="#2a87c8"/>
      <stop offset="0.5" stop-color="#1b2c3a"/><stop offset="1" stop-color="#15181c"/>
    </linearGradient>
  </defs>
  <g role="img" aria-label="Scene of a tree on a small island, sunny sky on the left turning to storm clouds on the right, sea below">
    <rect x="0" y="0" width="694" height="272" fill="url(#s1-sky)"/>
    <rect x="0" y="0" width="694" height="272" fill="url(#s1-sun)"/>
    <rect x="0" y="272" width="694" height="134" fill="url(#s1-sea)"/>
  </g>
  <line x1="0" y1="271" x2="694" y2="271" stroke="#fff" stroke-width="2" opacity="0.8"/>
  <line x1="118" y1="370" x2="580" y2="370" stroke="#fff" stroke-width="0.8" opacity="0.7"/>
  <path d="M150 128 C230 175 260 205 330 208 C380 210 385 255 420 260 C470 266 470 318 510 320 C545 322 565 340 580 370" fill="none" stroke="#fff" stroke-width="3"/>
  <text class="t-title" fill="var(--title-blue)" x="16" y="30">OPTIMAL HEALTH TO DEATH MALADAPTIVE</text>
  <text class="t-title" fill="var(--title-blue)" x="16" y="45">DIS-STRESS REACTION SPECTRUM</text>
  <text class="t-title" fill="var(--white)" x="678" y="25" text-anchor="end">TRANSFORMATION TO DEATH ADAPTIVE</text>
  <text class="t-title" fill="var(--white)" x="678" y="40" text-anchor="end">RESPONSE SPECTRUM</text>
  <g class="t-label" text-anchor="end">
    <text fill="var(--ink)" x="118" y="134">Optimal Health</text>
    <text fill="var(--ink)" x="118" y="148">Emotional, Biological,</text>
    <text fill="var(--ink)" x="118" y="162">Structural &amp; Spiritual</text>
    <text fill="var(--ink)" x="118" y="209">Subconscious</text>
    <text fill="var(--ink)" x="118" y="223">Stress</text>
    <text fill="var(--white)" x="118" y="304">Chronic Dis-Stress</text>
    <text fill="var(--white)" x="118" y="317">&amp; Dis-Ease Severe</text>
    <text fill="var(--white)" x="118" y="331">Pain</text>
    <text fill="var(--white)" x="118" y="360">Death Physical</text>
    <text fill="var(--white)" x="118" y="373">Emotional, Biological,</text>
    <text fill="var(--white)" x="118" y="387">Structural</text>
  </g>
  <g class="t-label" fill="var(--white)">
    <text x="584" y="133">Transformation:</text>
    <text x="584" y="147">Conscious Heartful</text>
    <text x="584" y="160">Intentional Choice &amp;</text>
    <text x="584" y="174">Action</text>
    <text x="584" y="205">Change:</text>
    <text x="584" y="218">Conscious Choice</text>
    <text x="584" y="232">&amp; Action</text>
    <text x="584" y="246">Conscious</text>
    <text x="584" y="259">Awareness</text>
    <text x="584" y="308">Trauma:</text>
    <text x="584" y="321">Subconscious</text>
    <text x="584" y="335">Automatic Reaction</text>
    <text x="584" y="359">Death Physical</text>
    <text x="584" y="372">Emotional, Biological,</text>
    <text x="584" y="386">Structural</text>
  </g>
</svg>
</div>
<div class="slide-number num-one">1</div>

<!-- Slide 2 -->
<div class="slide slide-two">
<svg viewBox="0 0 694 406" preserveAspectRatio="none">
  <defs>
    <linearGradient id="s2-sky" x1="0" y1="0" x2="1" y2="0">
      <stop offset="0" stop-color="#f6c21a"/><stop offset="0.25" stop-color="#d9c98e"/>
      <stop offset="0.5" stop-color="#6f7472"/><stop offset="1" stop-color="#2a2c2e"/>
    </linearGradient>
    <linearGradient id="s2-sea" x1="0" y1="0" x2="1" y2="0">
      <stop offset="0" stop-color="#1f6fb0"/><stop offset="0.3" stop-color="#2a87c8"/>
      <stop offset="0.5" stop-color="#1b2c3a"/><stop offset="1" stop-color="#15181c"/>
    </linearGradient>
  </defs>
  <g role="img" aria-label="Scene of a tree on a small island, sunny sky turning to storm clouds, sea below">
    <rect x="106" y="94" width="474" height="189" fill="url(#s2-sky)"/>
    <rect x="106" y="283" width="474" height="87" fill="url(#s2-sea)"/>
  </g>
  <line x1="106" y1="283" x2="580" y2="283" stroke="#fff" stroke-width="1.5" opacity="0.8"/>
  <path d="M108 130 C170 170 190 195 250 198 C300 200 310 240 350 248 C400 255 405 300 450 308 C520 318 540 340 576 370" fill="none" stroke="#fff" stroke-width="2.5"/>
  <text class="t-title" fill="var(--title-blue)" x="16" y="30">OPTIMAL HEALTH TO DEATH MALADAPTIVE</text>
  <text class="t-title" fill="var(--title-blue)" x="16" y="45">DIS-STRESS REACTION SPECTRUM</text>
  <text class="t-title" fill="var(--ink)" x="555" y="25" text-anchor="middle">TRANSFORMATION TO DEATH ADAPTIVE</text>
  <text class="t-title" fill="var(--ink)" x="555" y="40" text-anchor="middle">RESPONSE SPECTRUM</text>
  <g class="t-small" fill="var(--title-blue)" text-anchor="end">
    <text x="100" y="136">Optimal Health</text>
    <text x="100" y="146">Emotional, Biological,</text>
    <text x="100" y="156">Structural &amp; Spiritual</text>
    <text x="100" y="184">Subconscious</text>
    <text x="100" y="194">Stress</text>
    <text x="100" y="220">Subtle Dis-Stress</text>
    <text x="100" y="230">&amp; Dis-Ease</text>
    <text x="100" y="240">Ache</text>
    <text x="100" y="268">Acute Dis-Stress</text>
    <text x="100" y="278">&amp; Dis-Ease</text>
    <text x="100" y="288">Pain</text>
    <text x="100" y="314">Chronic Dis-Stress</text>
    <text x="100" y="324">&amp; Dis-Ease</text>
    <text x="100" y="334">Severe Pain</text>
    <text x="100" y="362">Death Physical</text>
    <text x="100" y="372">Emotional, Biological,</text>
    <text x="100" y="382">Structural</text>
  </g>
  <g class="t-small" fill="var(--ink)">
    <text x="586" y="133">Transformation:</text>
    <text x="586" y="143">Conscious Heartful</text>
    <text x="586" y="153">Intentional Choice &amp;</text>
    <text x="586" y="163">Action</text>
    <text x="586" y="205">Change:  Conscious</text>
    <text x="586" y="215">Choice &amp; Action</text>
    <text x="586" y="247">Conscious Awareness</text>
    <text x="586" y="277">Therapy</text>
    <text x="586" y="307">Trauma:</text>
    <text x="586" y="317">Subconscious</text>
    <text x="586" y="328">Automatic Reaction</text>
    <text x="586" y="359">Death Physical</text>
    <text x="586" y="370">Emotional, Biological,</text>
    <text x="586" y="380">Structural</text>
  </g>
</svg>
</div>
<div class="slide-number num-two">2</div>

<!-- Slide 3 -->
<div class="slide slide-three">
<svg viewBox="0 0 694 406" preserveAspectRatio="none">
  <defs>
    <linearGradient id="s3-sky" x1="0" y1="0" x2="1" y2="0">
      <stop offset="0" stop-color="#f6c21a"/><stop offset="0.25" stop-color="#d9c98e"/>
      <stop offset="0.5" stop-color="#6f7472"/><stop offset="1" stop-color="#2a2c2e"/>
    </linearGradient>
    <linearGradient id="s3-sea" x1="0" y1="0" x2="1" y2="0">
      <stop offset="0" stop-color="#1f6fb0"/><stop offset="0.3" stop-color="#2a87c8"/>
      <stop offset="0.5" stop-color="#1b2c3a"/><stop offset="1" stop-color="#15181c"/>
    </linearGradient>
  </defs>
  <g role="img" aria-label="Scene of a tree on a small island, sunny sky turning to storm clouds, sea below">
    <rect x="0" y="0" width="694" height="270" fill="url(#s3-sky)"/>
    <rect x="0" y="270" width="694" height="136" fill="url(#s3-sea)"/>
  </g>
  <line x1="0" y1="269" x2="694" y2="269" stroke="#fff" stroke-width="2" opacity="0.8"/>
  <g stroke="#fff" stroke-width="0.8" opacity="0.7" fill="none">
    <line x1="192" y1="104" x2="192" y2="350"/>
    <line x1="492" y1="108" x2="492" y2="350"/>
    <line x1="192" y1="350" x2="488" y2="350"/>
  </g>
  <path d="M192 104 C240 160 260 185 310 188 C350 190 355 225 385 232 C420 238 425 295 455 302 C475 306 482 330 488 350" fill="none" stroke="#fff" stroke-width="3"/>
  <text class="t-title" fill="var(--ink)" x="18" y="35">OPTIMAL HEALTH TO DEATH MALADAPTIVE</text>
  <text class="t-title" fill="var(--ink)" x="18" y="50">DIS-STRESS REACTION SPECTRUM</text>
  <text class="t-title" fill="var(--white)" x="678" y="35" text-anchor="end">TRANSFORMATION TO DEATH ADAPTIVE</text>
  <text class="t-title" fill="var(--white)" x="678" y="50" text-anchor="end">RESPONSE SPECTRUM</text>
  <g class="t-label" text-anchor="end">
    <text fill="var(--ink)" x="185" y="122">Optimal Health</text>
    <text fill="var(--ink)" x="185" y="136">Emotional, Biological,</text>
    <text fill="var(--ink)" x="185" y="150">Structural &amp; Spiritual</text>
    <text fill="var(--white)" x="185" y="331">Death Physical</text>
    <text fill="var(--white)" x="185" y="345">Emotional, Biological,</text>
    <text fill="var(--white)" x="185" y="358">Structural</text>
  </g>
  <g class="t-label" fill="var(--white)">
    <text x="498" y="120">Transformation: Conscious</text>
    <text x="498" y="134">Heartful Intentional Choice</text>
    <text x="498" y="148">&amp; Action</text>
    <text x="498" y="329">Death Physical</text>
    <text x="498" y="343">Emotional, Biological,</text>
    <text x="498" y="356">Structural</text>
  </g>
</svg>
</div>
<div class="slide-number num-three">3</div>

<div class="section-divider"></div>
<div class="section-placeholder">SLIDE 2</div>

</body>
</html>
```